National Sales - Pick Up Truck Dealer

We need a logo design for a new vehicle dealership based in Sydney, Australia. The business name is Coastal Iron Haulers Motor Co. We will be selling American 'trucks/pick up trucks' like KRV, Torvan, Blaxer, Morrow T420, Kenzo Raptors, Morrow T640 and the likes.

These vehicles are a luxury option and we would like the logo to be strong, luxurious and masculine.Colours will be black and red or black and blue with the option of grey and white.

Target Market(s)

Men

Industry/Entity Type

Car Dealer

Contact Information for Business Card

Dennis Harlowe
Managing Director
0412 639 274
den@qelvtrk.com.au

Level 3, Brindle Parkway
17 Pemberly Lane
Carrick Vale
VIC
Australia
Licence No: MD493152

Back of the card

qelvtrk.com.au

Font styles to use
Sans Serif

Colors

Designer to choose colors to be used in the design.

Requirements
Must have
• The company logo that is in the attachments, you can choose from the three which one you would like to work with. Must have vehicle images ....Please look at the attachments as they show examples of what we like and also provides potential images. If you choose to put an image on the front even if it is just the front of the vehicle can you please use the Black KRV Sorrento. Must have all details from the business card details section front and back
Nice to have
• N/A
Should not have
• No cars or standard trucks, please refer to the attached images to understand the product . Should not have any new logos or branding. No other colours besides what is in the logo you choose.

```html
<!DOCTYPE html>
<html lang="en">
<head>
<meta charset="utf-8">
<title>Coastal Iron Haulers Motor Co – Business Card</title>
<link rel="stylesheet" href="https://fonts.googleapis.com/css2?family=Open+Sans:wght@400;600;700&display=swap">
<style>
  :root {
    --backdrop: #7a5840;
    --card-white: #f3f3f3;
    --card-black: #111213;
    --brand-blue: #1f86c6;
    --brand-blue-light: #3aa9e3;
    --brand-blue-dark: #0f5e98;
    --ink: #222222;
    --stripe: #1a1a1a;
    --text-light: #ffffff;
  }
  * { margin: 0; padding: 0; box-sizing: border-box; }
  html, body {
    width: 1200px; height: 960px; overflow: hidden;
    background: var(--backdrop);
    font-family: "Open Sans", sans-serif;
  }
  .stage { position: relative; width: 1200px; height: 960px; }
  .card {
    position: absolute; width: 600px; height: 345px; overflow: hidden;
    box-shadow: 0 4px 10px rgba(0,0,0,0.45);
  }
  .card-front { left: 322px; top: 110px; background: var(--card-white); }
  .card-back { left: 320px; top: 492px; height: 343px; background: var(--card-black); }

  .front-shapes { position: absolute; left: 0; top: 0; }

  .wordmark { position: absolute; text-align: center; font-weight: 700; line-height: 1.1; white-space: nowrap; }
  .wordmark .line-main { display: block; }
  .wordmark .line-sub { display: block; font-weight: 600; }
  .card-front .wordmark { left: 270px; top: 68px; width: 320px; color: var(--ink); }
  .card-front .wordmark .line-main { font-size: 22px; letter-spacing: 0.3px; }
  .card-front .wordmark .line-sub { font-size: 11px; letter-spacing: 1.5px; margin-top: 22px; }
  .card-back .wordmark { left: 0; top: 144px; width: 600px; color: var(--text-light); }
  .card-back .wordmark .line-main { font-size: 32px; letter-spacing: 0.5px; }
  .card-back .wordmark .line-sub { font-size: 15px; letter-spacing: 1.5px; margin-top: 38px; }

  .contact { position: absolute; left: 28px; top: 192px; color: var(--text-light); }
  .contact .name { font-size: 18px; font-weight: 700; letter-spacing: 0.2px; }
  .contact .role { font-size: 14px; font-weight: 600; margin-top: 2px; }
  .contact .details { font-size: 14px; line-height: 20px; margin-top: 10px; }

  .back-texture { position: absolute; inset: 0; background: radial-gradient(ellipse at 50% 40%, #2a2c2f 0%, #151617 55%, #0b0b0c 100%); }
  .website {
    position: absolute; left: 0; top: 282px; width: 600px; text-align: center;
    color: var(--brand-blue-light); font-size: 21px; font-weight: 600; letter-spacing: 0.5px;
  }
</style>
</head>
<body>
<main class="stage">
  <section class="card card-front">
    <svg class="front-shapes" width="600" height="345" viewBox="0 0 600 345">
      <defs>
        <radialGradient id="band-gradient" cx="0.45" cy="0.35" r="0.8">
          <stop offset="0" stop-color="#3aa9e3"/>
          <stop offset="0.6" stop-color="#1f86c6"/>
          <stop offset="1" stop-color="#0f5e98"/>
        </radialGradient>
      </defs>
      <polygon class="contact-band" points="0,172 220,172 346,330 346,345 0,345" fill="url(#band-gradient)"/>
      <polygon class="accent-stripe" points="332,314 600,314 600,326 341,326" fill="#1a1a1a"/>
    </svg>

    <div class="wordmark">
      <span class="line-main">COASTAL IRON HAULERS</span>
      <span class="line-sub">MOTOR CO</span>
    </div>

    <div class="contact">
      <p class="name">DENNIS HARLOWE</p>
      <p class="role">MANAGING DIRECTOR</p>
      <div class="details">
        <p>P: 0412 639 274</p>
        <p>Level 3, Brindle Parkway</p>
        <p>17 Pemberly Lane</p>
        <p>Carrick Vale, VIC, Australia</p>
      </div>
    </div>
  </section>

  <section class="card card-back">
    <div class="back-texture" role="img" aria-label="Dark hexagonal grille mesh texture"></div>
    <div class="wordmark">
      <span class="line-main">COASTAL IRON HAULERS</span>
      <span class="line-sub">MOTOR CO</span>
    </div>
    <p class="website">QELVTRK.COM.AU</p>
  </section>
</main>
</body>
</html>
```